Business Card Design Project

We are rebranding an existing automotive collision repair business. The business is called dent haven. I have attached logo but I'm not tied to that. I want to leave this wide open.

I want this card to say we are professional, competent, cutting edge. We are focused on customers and use a lot of the latest technology to make the customer experience different. We sign customers in on iPads. Paperwork I signed electronically and updates are sent via text, email, logging on a website or as they wish. I want this innovation and image to come through in our cards

Target Market(s)

60%. Women 40% men. Age 35-60

Industry/Entity Type

Automotive

Requirements
Must have
• The card must have name, title, phone,email, cell, web page

```html
<!DOCTYPE html>
<html lang="en">
<head>
<meta charset="utf-8">
<title>Dent Haven – Business Card</title>
<link rel="stylesheet" href="https://fonts.googleapis.com/css2?family=Roboto:wght@300;400&display=swap">
<style>
  :root {
    --page: #ffffff;
    --card-light: #f4f4f4;
    --brand-green: #7bc142;
    --brand-green-text: #6cb33c;
    --faint-green: #dcecd3;
    --white: #ffffff;
  }
  * { margin: 0; padding: 0; box-sizing: border-box; }
  html, body {
    width: 1200px;
    height: 800px;
    overflow: hidden;
    background: var(--page);
    font-family: "Roboto", Arial, sans-serif;
    font-weight: 300;
  }
  .canvas {
    position: relative;
    width: 1200px;
    height: 800px;
  }
  .card {
    position: absolute;
    top: 278px;
    width: 424px;
    height: 243px;
    overflow: hidden;
    box-shadow: 0 14px 16px -10px rgba(0,0,0,0.35);
  }
  .card--front { left: 128px; background: var(--card-light); }
  .card--back  { left: 638px; background: var(--brand-green); }

  /* front */
  .holder {
    position: absolute;
    right: 256px;
    top: 99px;
    text-align: right;
    color: var(--brand-green-text);
  }
  .holder__name { font-size: 22px; line-height: 26px; }
  .holder__title { font-size: 14px; line-height: 16px; }
  .front-wordmark {
    position: absolute;
    left: 186px;
    top: 103px;
    font-size: 30px;
    letter-spacing: 0.5px;
    color: var(--faint-green);
    white-space: nowrap;
  }

  /* back */
  .brand {
    position: absolute;
    right: 22px;
    top: 50px;
    display: flex;
    align-items: center;
    gap: 6px;
    color: var(--white);
    font-size: 12px;
    font-weight: 400;
    letter-spacing: 0.3px;
  }
  .brand__dot {
    width: 9px;
    height: 9px;
    border-radius: 50%;
    background: var(--white);
  }
  .contacts {
    position: absolute;
    left: 22px;
    top: 125px;
    list-style: none;
    color: var(--white);
    font-size: 13px;
  }
  .contacts li {
    display: flex;
    align-items: center;
    height: 22.3px;
  }
  .contacts svg {
    width: 14px;
    height: 14px;
    margin-right: 11px;
    fill: none;
    stroke: var(--white);
    stroke-width: 1.2;
  }
</style>
</head>
<body>
<main class="canvas">

  <section class="card card--front" aria-label="Card front">
    <div class="front-wordmark">DENT HAVEN</div>
    <div class="holder">
      <p class="holder__name">Mara Keswick</p>
      <p class="holder__title">Director</p>
    </div>
  </section>

  <section class="card card--back" aria-label="Card back">
    <div class="brand">
      <span class="brand__dot"></span>
      <span class="brand__name">DENT HAVEN</span>
    </div>
    <ul class="contacts">
      <li>
        <svg viewBox="0 0 14 14"><rect x="1" y="3" width="12" height="8"/><path d="M1 3l6 5 6-5"/></svg>
        hello@denthaven.com
      </li>
      <li>
        <svg viewBox="0 0 14 14"><circle cx="7" cy="7" r="6"/><ellipse cx="7" cy="7" rx="2.6" ry="6"/><path d="M1 7h12M2 4h10M2 10h10"/></svg>
        www.denthaven.com
      </li>
      <li>
        <svg viewBox="0 0 14 14"><path d="M3 1.5l2.2 2.5-1.3 1.6c.8 1.8 2.2 3.2 4 4l1.6-1.3 2.5 2.2-1.5 1.8C6 12 2 8 1.7 3z"/></svg>
        +1 (800) 555-0142
      </li>
      <li>
        <svg viewBox="0 0 14 14"><rect x="3.5" y="0.8" width="7" height="12.4" rx="1"/><path d="M6 11h2"/></svg>
        +1 (800) 555-0142
      </li>
    </ul>
  </section>

</main>
</body>
</html>
```